The most modern business card ever !!!

Our company call “Vendalo”. Vendalo is a technology company specialized in cruises solutions. Out main product is a platform to reserve cruises. This is a revolutionary platform that make easier to travel agencies and final users to reserve cruises across dozen companies like tibba, wernu, hpv, dgb, etc..We are a “start up”, with a young team of developers and we want to transmit it.. For it, we want something different, a modern business card that represent cruises and technology.. When someone receive this card, this person should say: wowww this is different… this is modern… this is a cruise related company..
- diferent, modern
- traditions business card

```html
<!DOCTYPE html>
<html lang="en">
<head>
<meta charset="utf-8">
<title>Vendalo – Business Card</title>
<link href="https://fonts.googleapis.com/css2?family=Exo+2:wght@500&family=Raleway:wght@600&family=Open+Sans:wght@700&display=swap" rel="stylesheet">
<style>
  :root {
    --backdrop: #d9d6d1;
    --card: #141414;
    --card-edge: #2b2b2b;
    --logo-text: #e4e6e8;
    --name-text: #e2e2e2;
    --detail-text: #f0f0f0;
    --accent-blue: #1ba4dc;
    --gold-light: #f0d9a8;
    --gold-mid: #c79c5c;
    --gold-dark: #7a5a2e;
  }
  * { margin: 0; padding: 0; box-sizing: border-box; }
  html, body {
    width: 1200px;
    height: 663px;
    overflow: hidden;
    background: var(--backdrop);
  }
  .canvas {
    position: relative;
    width: 1200px;
    height: 663px;
  }
  .card {
    position: absolute;
    top: 180px;
    width: 430px;
    height: 250px;
    background: var(--card);
    border: 1px solid var(--card-edge);
    border-radius: 22px;
    box-shadow: 0 10px 28px rgba(0, 0, 0, 0.35);
    overflow: hidden;
  }
  .card--front { left: 110px; }
  .card--back { left: 716px; }
  .card__chevron {
    position: absolute;
    inset: 0;
    width: 100%;
    height: 100%;
  }
  .brand-name {
    position: absolute;
    left: 91px;
    top: 96px;
    font-family: "Exo 2", sans-serif;
    font-weight: 500;
    font-size: 47px;
    letter-spacing: 2px;
    line-height: 1;
    color: var(--logo-text);
  }
  .contact {
    position: absolute;
    left: 157px;
    top: 84px;
  }
  .contact__name {
    font-family: "Raleway", sans-serif;
    font-weight: 600;
    font-size: 19px;
    letter-spacing: 0.5px;
    color: var(--name-text);
    margin-bottom: 19px;
  }
  .contact__line {
    display: flex;
    align-items: center;
    gap: 8px;
    font-family: "Open Sans", sans-serif;
    font-weight: 700;
    font-size: 12px;
    color: var(--detail-text);
    height: 24px;
  }
  .contact__icon { width: 15px; height: 12px; flex: none; }
</style>
</head>
<body>
<main class="canvas">

  <section class="card card--front" aria-label="Card front">
    <svg class="card__chevron" viewBox="0 0 430 250" aria-hidden="true">
      <defs>
        <linearGradient id="goldFront" x1="0" y1="0" x2="1" y2="1">
          <stop offset="0" stop-color="var(--gold-dark)"/>
          <stop offset="0.5" stop-color="var(--gold-light)"/>
          <stop offset="1" stop-color="var(--gold-mid)"/>
        </linearGradient>
      </defs>
      <polygon points="301,49 339,49 417,124 339,202 301,202 379,124"
               fill="url(#goldFront)" stroke="#3a3a3a" stroke-width="1.5"/>
    </svg>
    <p class="brand-name">Vendalo</p>
  </section>

  <section class="card card--back" aria-label="Card back">
    <svg class="card__chevron" viewBox="0 0 430 250" aria-hidden="true">
      <defs>
        <linearGradient id="goldBack" x1="1" y1="0" x2="0" y2="1">
          <stop offset="0" stop-color="var(--gold-dark)"/>
          <stop offset="0.5" stop-color="var(--gold-light)"/>
          <stop offset="1" stop-color="var(--gold-mid)"/>
        </linearGradient>
      </defs>
      <polygon points="85,49 130,49 51,124 130,202 85,202 13,124"
               fill="url(#goldBack)" stroke="#3a3a3a" stroke-width="1.5"/>
    </svg>

    <div class="contact">
      <p class="contact__name">YOUR NAME</p>
      <p class="contact__line">
        <svg class="contact__icon" viewBox="0 0 15 12" aria-hidden="true">
          <path d="M1 4 Q7.5 -1 14 4 L12 5.5 L10.5 4 L4.5 4 L3 5.5 Z" fill="var(--accent-blue)"/>
          <rect x="2.5" y="6" width="10" height="5.5" rx="1" fill="var(--accent-blue)"/>
          <circle cx="7.5" cy="8.7" r="1.4" fill="var(--card)"/>
        </svg>
        <span>000 000 0000</span>
      </p>
      <p class="contact__line">
        <svg class="contact__icon" viewBox="0 0 15 12" aria-hidden="true">
          <rect x="0.5" y="1" width="14" height="10" fill="var(--accent-blue)"/>
          <path d="M0.5 1 L7.5 7 L14.5 1" fill="none" stroke="var(--card)" stroke-width="1.2"/>
        </svg>
        <span>youremail@xyz.com</span>
      </p>
    </div>
  </section>

</main>
</body>
</html>
```